Need a cover for eBook:
Title is: 52 Blunders That Sink Your Indie-Released eBook.
Remarks about the title: I know that is difficult to design a cover with a number. You can add the word TOP (in caps or not) before 69 mistakes. It is not mandatory to insert the word TOP. It is up to you if you think you can create a better cover.
Subtitle is: A Starter's Handbook for Releasing Solo, Arranging Pictures and Words, Planning Pages, Raising Signups and Moving More Copies
Author: Walter P. Brenshaw
Publisher: Quillmark Works
The book made the presentation of errors that can occur during the production of an ebook. Title must be big, the title should be readable even when the image is reduced in size. No photo please.
I join my projects as an example. Do what you want but I need impact.

Target Market(s)

Book to sell first at Borvela Reader Shop. Target is authors, men or women, who want to produce ebooks.

Industry/Entity Type

Publishing Company

Font styles to use
Sans Serif

Colors
3176b5
9bcb3c

Requirements
Must have
• High readability when cover is small.
• Here is the definition of the word KILL
• put an end to or cause the failure or defeat of (something).
• "the committee voted to kill the project"
• synonyms: destroy, put an end to, end, extinguish, dash, quash, ruin, wreck, shatter, smash, crush, scotch, thwart; informalput the kibosh on, stymie, scuttle
• "this would kill all hopes of progress"
• veto, defeat, vote down, rule against, reject, throw out, overrule, overturn, put a stop to, quash, squash
• "an opposition attempt to kill the bill"
Nice to have
• I suggested 2 colors but you can you use another one or two. I want cover that sell. There is so bright ideas here. Come on down!
Should not have
• No picture or photo. If a photo or an object had power to the cover, you can insert one. I don't want a photo-collage.

```html
<!DOCTYPE html>
<html lang="en">
<head>
<meta charset="utf-8">
<title>52 Blunders That Sink Your Indie-Released eBook — Cover</title>
<link rel="stylesheet" href="https://fonts.googleapis.com/css2?family=Anton&family=Archivo+Black&family=Archivo:wght@800&family=EB+Garamond:wght@700;800&display=swap">
<style>
  :root {
    --ink: #000000;
    --paper: #ffffff;
    --lime: #9bcb3c;
    --lime-light: #c4e85e;
    --lime-deep: #6f9d22;
    --lime-edge: #35530d;
    --burst-blue: #3176b5;
    --burst-edge: #e0283a;
  }
  html, body {
    margin: 0;
    padding: 0;
    width: 927px;
    height: 1200px;
    overflow: hidden;
    background: var(--ink);
  }
  .cover {
    display: block;
    width: 927px;
    height: 1200px;
    background: var(--ink);
  }
  .title-number {
    font-family: "Archivo Black", "Arial Black", sans-serif;
    font-size: 238px;
    fill: url(#limeBevel);
    stroke: var(--lime-edge);
    stroke-width: 4;
    paint-order: stroke fill;
  }
  .title-number-shade {
    font-family: "Archivo Black", "Arial Black", sans-serif;
    font-size: 238px;
    fill: var(--lime-edge);
  }
  .title-word {
    font-family: "Anton", "Impact", sans-serif;
    font-size: 150px;
    fill: url(#limeBevel);
    stroke: var(--lime-edge);
    stroke-width: 3;
    paint-order: stroke fill;
  }
  .title-word-shade {
    font-family: "Anton", "Impact", sans-serif;
    font-size: 150px;
    fill: var(--lime-edge);
  }
  .title-tail {
    font-family: "Anton", "Impact", sans-serif;
    font-size: 62px;
    fill: var(--ink);
    stroke: var(--paper);
    stroke-width: 4;
    paint-order: stroke fill;
  }
  .subtitle-line {
    font-family: "EB Garamond", "Garamond", serif;
    font-weight: 800;
    font-size: 30px;
    fill: var(--ink);
    stroke: var(--paper);
    stroke-width: 3;
    paint-order: stroke fill;
  }
  .burst {
    fill: var(--burst-blue);
    stroke: var(--burst-edge);
    stroke-width: 4;
    stroke-linejoin: miter;
  }
  .burst-small {
    font-family: "EB Garamond", "Garamond", serif;
    font-weight: 700;
    font-size: 28px;
    fill: var(--ink);
  }
  .burst-accent {
    font-family: "EB Garamond", "Garamond", serif;
    font-weight: 800;
    font-size: 46px;
    fill: var(--lime);
  }
  .author-name,
  .publisher-name {
    font-family: "Archivo", "Arial", sans-serif;
    font-weight: 800;
    font-size: 31px;
    fill: var(--paper);
  }
</style>
</head>
<body>
<svg class="cover" viewBox="0 0 927 1200" width="927" height="1200" role="img" aria-label="Cover: 52 Blunders That Sink Your Indie-Released eBook by Walter P. Brenshaw">
  <defs>
    <linearGradient id="limeBevel" x1="0" y1="0" x2="0" y2="1">
      <stop offset="0" stop-color="var(--lime-light)"/>
      <stop offset="0.45" stop-color="var(--lime)"/>
      <stop offset="1" stop-color="var(--lime-deep)"/>
    </linearGradient>
  </defs>

  <rect class="backdrop" x="0" y="0" width="927" height="1200" fill="var(--ink)"/>

  <g class="title">
    <text class="title-number-shade" x="470" y="228" text-anchor="middle" textLength="572" lengthAdjust="spacingAndGlyphs">52</text>
    <text class="title-number" x="466" y="222" text-anchor="middle" textLength="572" lengthAdjust="spacingAndGlyphs">52</text>

    <text class="title-word-shade" x="488" y="359" text-anchor="middle" textLength="536" lengthAdjust="spacingAndGlyphs">Blunders</text>
    <text class="title-word" x="484" y="355" text-anchor="middle" textLength="536" lengthAdjust="spacingAndGlyphs">Blunders</text>

    <text class="title-tail" x="472" y="485" text-anchor="middle" textLength="407" lengthAdjust="spacingAndGlyphs">That Sink Your</text>
    <text class="title-tail" x="480" y="546" text-anchor="middle" textLength="434" lengthAdjust="spacingAndGlyphs">Indie-Released</text>
    <text class="title-tail" x="497" y="612" text-anchor="middle" textLength="160" lengthAdjust="spacingAndGlyphs">eBook</text>
  </g>

  <g class="burst-callout">
    <polygon class="burst" points="745,712 712,800 840,793 760,842 855,862 770,902 820,1030 705,955 655,1035 615,960 575,1005 560,960 435,1012 510,940 378,893 505,850 468,735 570,805 627,740 660,800"/>
    <text class="burst-small" x="640" y="856" text-anchor="middle">and</text>
    <text class="burst-accent" x="640" y="892" text-anchor="middle">Moving</text>
    <text class="burst-small" x="640" y="924" text-anchor="middle">More Copies</text>
  </g>

  <g class="subtitle">
    <text class="subtitle-line" x="98" y="785" textLength="340" lengthAdjust="spacingAndGlyphs">A Starter's Handbook for</text>
    <text class="subtitle-line" x="98" y="828">Releasing Solo,</text>
    <text class="subtitle-line" x="98" y="871" textLength="380" lengthAdjust="spacingAndGlyphs">Arranging Pictures and Words,</text>
    <text class="subtitle-line" x="98" y="914">Planning Pages,</text>
    <text class="subtitle-line" x="98" y="957">Raising Signups</text>
  </g>

  <g class="credits">
    <text class="author-name" x="72" y="1083" textLength="265" lengthAdjust="spacingAndGlyphs">Walter P. Brenshaw</text>
    <text class="publisher-name" x="603" y="1088" textLength="243" lengthAdjust="spacingAndGlyphs">Quillmark Works</text>
  </g>
</svg>
</body>
</html>
```